Wellness, Meaning, and the Inner Journey Research Program Website

Overview: This website will serve a new research program (Wellness, Meaning, and the Inner Journey) at the Harrowgate University School of Medicine. I want a clean, intuitive design that has a navigation bar, but uses icons/graphic buttons to link to the main pages. In an attached Word document, I have provided a basic information architecture for the site, understanding that this project would just generate graphics and code for the 3 pages. I highlighted the 3 pages I'd like designed.
Target market: People who want to participate in our research, or contribute grant funding to specific projects.
Number of page: The design project focuses on 3 pages, but the site must accommodate 6 pages with top-level links. See attached Word doc.
Logo and website header: Please integrate our logo in the header. I've uploaded it as a png file--both with the name of the website and with just the logo image. I imaging the logo would look great in a banner set against an image of a mountain. The two main design themes I want to see included are nature and healthcare.
Text content: I have not yet provided text. Use some dummy text.
Technical Specifications:
- Build using WordPress. We will host this site ourselves on NetHarbor using WordPress.
- The design package must be coded.
- The template must be responsive to different platforms (e.g., computer, mobile phone, iPad).
Thank you! I look forward to seeing your designs.
- Ned

```html
<!DOCTYPE html>
<html lang="en">
<head>
<meta charset="utf-8">
<title>Wellness, Meaning, and the Inner Journey</title>
<link href="https://fonts.googleapis.com/css2?family=Poppins:wght@300;400;700;800&family=Open+Sans:wght@400;600&family=Roboto:wght@500&display=swap" rel="stylesheet">
<style>
:root{
  --blue:#0b55a8;
  --blue-dark:#073f80;
  --teal:#12b3a5;
  --mint:#c4ebe8;
  --bg:#eef3f5;
  --text:#3b3f45;
  --muted:#6a6f76;
  --white:#fff;
}
*{box-sizing:border-box;margin:0;padding:0}
html,body{width:1200px;height:3193px;overflow:hidden}
body{position:relative;font-family:"Open Sans",sans-serif;color:var(--text);background:var(--white)}
.abs{position:absolute}
.topbar{left:0;top:0;width:1200px;height:54px;background:var(--blue);color:var(--white);font-size:13px}
.contact-item{position:absolute;top:18px;display:flex;align-items:center;gap:10px}
.nav{left:0;top:54px;width:1200px;height:79px;background:var(--white)}
.brand{position:absolute;left:16px;top:18px;display:flex;align-items:center;gap:10px}
.brand-mark{width:40px;height:40px;border-radius:50%;background:var(--teal)}
.brand-name{font-family:"Poppins",sans-serif;font-weight:700;font-size:10.5px;color:var(--blue);line-height:1.25;border-left:1px solid #9aa;padding-left:8px}
.nav-link{position:absolute;top:32px;font-size:12.5px;color:#333}
.btn{display:inline-flex;align-items:center;justify-content:center;background:var(--blue);color:var(--white);font-family:"Poppins",sans-serif;font-weight:700;font-size:11.5px;border-radius:5px;letter-spacing:-.2px}
.hero{left:0;top:133px;width:1200px;height:625px;background:linear-gradient(180deg,#3d5a3e 0%,#5e7d5a 40%,#8a8a80 70%,#4d5a48 100%)}
.hero h1{position:absolute;left:0;width:1200px;top:235px;text-align:center;font-family:"Poppins",sans-serif;font-weight:800;font-size:44px;line-height:44px;color:var(--white)}
.hero .btn{position:absolute;left:541px;top:346px;width:118px;height:42px;border:2px solid var(--white);font-weight:400;font-size:11.5px}
.main{left:0;top:758px;width:1200px;height:1610px;background:var(--bg);overflow:hidden}
.heading-light{font-family:"Poppins",sans-serif;font-weight:300;color:var(--blue)}
.heading-bold{font-family:"Poppins",sans-serif;font-weight:800;color:var(--blue)}
.body-text{font-size:12.6px;line-height:23.2px;color:var(--text);text-align:justify}
.sub-title{font-family:"Roboto",sans-serif;font-weight:500;font-size:22px;color:var(--blue);text-align:center}
.tab{position:absolute;top:331px;height:50px;border:1px solid #999;background:rgba(255,255,255,.5);display:flex;align-items:center;gap:10px;padding-left:26px;font-size:13px}
.blob-photo{position:absolute;border-radius:48% 52% 46% 54%/55% 45% 55% 45%}
.testimonials{left:0;top:2368px;width:1200px;height:521px;background:var(--bg);overflow:hidden}
.quote-card{position:absolute;top:183px;width:438px;height:142px;background:var(--blue);border:5px solid var(--white);color:var(--white);font-size:12.6px;line-height:25px;padding:22px 40px}
.quote-card::after{content:"";position:absolute;left:66px;bottom:-13px;border:8px solid transparent;border-top-color:var(--blue)}
.client{position:absolute;top:368px;display:flex;align-items:center;gap:12px}
.avatar{width:50px;height:50px;border-radius:50%;background:#c98a6a}
.client-name{font-family:"Open Sans",sans-serif;font-size:21px;color:#444}
.client-role{font-size:11px;color:#555}
.footer{left:0;top:2889px;width:1200px;height:304px;background:var(--white)}
.social{width:28px;height:28px;border-radius:6px;background:var(--teal)}
.foot-link{position:absolute;top:214px;font-size:12.5px;color:#444}
.dot{width:5px;height:5px;border-radius:50%;background:#bbb;display:inline-block;margin:0 4px}
</style>
</head>
<body>

<header class="abs topbar">
  <div class="contact-item" style="left:214px"><svg width="16" height="18" viewBox="0 0 16 18"><path d="M8 0a6 6 0 0 0-6 6c0 5 6 12 6 12s6-7 6-12a6 6 0 0 0-6-6zm0 8.5A2.5 2.5 0 1 1 8 3.5a2.5 2.5 0 0 1 0 5z" fill="#2fd3c0"/></svg>#1011 Lakeview City, US</div>
  <div class="contact-item" style="left:466px"><svg width="16" height="16" viewBox="0 0 16 16"><path d="M3 1l3 3-2 2c1 2 3 4 5 5l2-2 3 3-2 3C6 15 1 10 1 3z" fill="#2fd3c0"/></svg>+1 555 204 7781</div>
  <div class="contact-item" style="left:672px"><svg width="18" height="18" viewBox="0 0 18 18"><rect x="1" y="3" width="16" height="14" rx="2" fill="#2fd3c0"/><rect x="4" y="6" width="10" height="3" fill="#0b55a8"/></svg>+1 555 318 2406</div>
  <div class="contact-item" style="left:876px"><svg width="26" height="18" viewBox="0 0 26 18"><rect width="26" height="18" fill="#2fd3c0"/><path d="M0 0l13 10L26 0" stroke="#0b55a8" fill="none" stroke-width="1.5"/></svg>info@wmij.org</div>
</header>

<nav class="abs nav">
  <div class="brand"><div class="brand-mark"></div><div class="brand-name">Wellness, Meaning, and the Inner Journey<br><span style="color:var(--teal)">The Research Program</span></div></div>
  <span class="nav-link" style="left:329px">Home</span>
  <span class="nav-link" style="left:458px">About Us</span>
  <span class="nav-link" style="left:604px">Our Products</span>
  <span class="nav-link" style="left:772px">Services</span>
  <span class="nav-link" style="left:912px">Contact Us</span>
  <span class="btn abs" style="left:1000px;top:16px;width:183px;height:39px">Get In Touch &nbsp;&nbsp;&nbsp;&nbsp;&nbsp;&raquo;</span>
</nav>

<section class="abs hero" role="img" aria-label="Woman meditating in a yoga pose among rocks and tropical trees">
  <svg class="abs" style="left:20px;top:295px" width="24" height="36"><path d="M20 2L4 18l16 16" stroke="#12b3a5" stroke-width="4" fill="none"/></svg>
  <svg class="abs" style="left:1156px;top:295px" width="24" height="36"><path d="M4 2l16 16L4 34" stroke="#12b3a5" stroke-width="4" fill="none"/></svg>
  <h1>Come Experience The Inner<br>Strength!</h1>
  <span class="btn">Get In Touch</span>
  <span class="abs" style="left:574px;top:602px;width:10px;height:10px;border-radius:50%;background:var(--teal)"></span>
</section>

<section class="abs main">
  <svg class="abs" style="left:0;top:0" width="1200" height="1610">
    <path d="M0 0H310C250 40 170 40 120 60C70 80 40 130 0 150Z" fill="var(--mint)"/>
    <path d="M800 0H1200V440C1120 380 1110 250 1040 130C990 60 860 90 800 0Z" fill="var(--mint)"/>
    <path d="M1200 600C1140 640 1130 800 1200 840Z" fill="var(--mint)"/>
    <path d="M0 800C80 860 60 1040 160 1100C260 1160 420 1240 520 1330C430 1390 260 1400 140 1440C60 1470 30 1550 0 1560Z" fill="var(--mint)"/>
  </svg>
  <div class="abs" style="left:146px;top:76px">
    <div class="heading-light" style="font-size:28px;line-height:32px">Welcome To</div>
    <div class="heading-bold" style="font-size:34px;line-height:36px">Wellness, Meaning, And<br>The Inner Journey</div>
    <svg width="80" height="16" style="margin-top:8px"><line x1="0" y1="8" x2="80" y2="8" stroke="var(--blue)" stroke-width="2.5"/><rect x="34" y="2" width="12" height="12" transform="rotate(45 40 8)" fill="var(--blue)"/></svg>
  </div>
  <p class="abs body-text" style="left:146px;top:210px;width:447px">Lorem ipsum dolor sit amet, consectetur adipiscing elit, sed do eiusmod tempor incididunt ut labore et dolore magna aliqua. Vulputate dignissim suspendisse in est ante. Faucibus turpis in eu mi bibendum neque. Sodales ut etiam sit amet nisl purus. Velit laoreet id donec ultrices tincidunt.</p>
  <div class="tab" style="left:146px;width:159px;color:#222"><svg width="30" height="30" viewBox="0 0 30 30"><path d="M5 25l6-3 12-12c2-3 3-6 2-8-2-1-5 0-8 2L5 16zM9 18l3 3" stroke="var(--teal)" stroke-width="2" fill="none"/></svg>Our Mission</div>
  <div class="tab" style="left:316px;width:159px;color:#555"><svg width="30" height="30" viewBox="0 0 30 30"><circle cx="15" cy="15" r="12" stroke="var(--teal)" stroke-width="2" fill="none"/><circle cx="15" cy="15" r="7" stroke="var(--teal)" stroke-width="2" fill="none"/><circle cx="15" cy="15" r="2" fill="var(--teal)"/></svg>Our Vission</div>
  <p class="abs" style="left:146px;top:404px;width:440px;font-size:12.6px;line-height:19px;color:var(--muted)">Lorem ipsum dolor sit amet, consectetur adipiscing elit, sed do eiusmod tempor incididunt ut labore et dolore magna aliqua.</p>
  <span class="btn abs" style="left:146px;top:490px;width:172px;height:40px">Know More About Us &raquo;</span>
  <div class="abs" role="img" aria-label="Woman with long hair meditating in a lotus pose" style="left:670px;top:97px;width:530px;height:577px;background:linear-gradient(180deg,rgba(255,255,255,0) 0%,#e6dcd4 40%,#cdb6a6 70%,#7a4f5a 100%);border-radius:60% 0 0 40%/50% 0 0 30%"></div>

  <div class="abs" style="left:0;top:570px;width:1200px;text-align:center"><span class="heading-light" style="font-size:27px">We </span><span class="heading-bold" style="font-size:36px">People</span></div>
  <svg class="abs" style="left:561px;top:616px" width="80" height="16"><line x1="0" y1="8" x2="80" y2="8" stroke="var(--blue)" stroke-width="2.5"/><rect x="34" y="2" width="12" height="12" transform="rotate(45 40 8)" fill="var(--blue)"/></svg>

  <div class="blob-photo" role="img" aria-label="Team of medical staff in scrubs and masks" style="left:155px;top:668px;width:428px;height:316px;background:linear-gradient(135deg,#9aa7ad,#4f7faa 60%,#d7dde0)"></div>
  <div class="abs sub-title" style="left:607px;top:672px;width:447px">Research</div>
  <p class="abs body-text" style="left:607px;top:714px;width:447px">Lorem ipsum dolor sit amet, consectetur adipiscing elit, sed do eiusmod tempor incididunt ut labore et dolore magna aliqua. Tempor orci eu lobortis elementum nibh tellus molestie. Sagittis orci a scelerisque purus semper eget duis at. Commodo odio aenean sed adipiscing diam donec. Faucibus scelerisque eleifend donec pretium vulputate sapien. Cursus vitae congue mauris rhoncus aenean vel elit scelerisque mauris. Ultrices gravida dictum fusce ut placerat. Volutpat commodo sed egestas egestas fringilla phasellus faucibus.</p>
  <span class="btn abs" style="left:931px;top:939px;width:122px;height:40px">Know More &raquo;</span>

  <div class="abs sub-title" style="left:146px;top:1031px;width:447px">Advisory Committee</div>
  <p class="abs body-text" style="left:146px;top:1073px;width:447px">Lorem ipsum dolor sit amet, consectetur adipiscing elit, sed do eiusmod tempor incididunt ut labore et dolore magna aliqua. Tempor orci eu lobortis elementum nibh tellus molestie. Sagittis orci a scelerisque purus semper eget duis at. Commodo odio aenean sed adipiscing diam donec. Faucibus scelerisque eleifend donec pretium vulputate sapien. Cursus vitae congue mauris rhoncus aenean vel elit scelerisque mauris. Ultrices gravida dictum fusce ut placerat. Volutpat commodo sed egestas egestas fringilla phasellus faucibus.</p>
  <span class="btn abs" style="left:471px;top:1298px;width:122px;height:40px">Know More &raquo;</span>
  <div class="blob-photo" role="img" aria-label="Business people reviewing charts at a meeting table" style="left:611px;top:1027px;width:424px;height:314px;background:linear-gradient(135deg,#d9e2ea,#8fa3b6 50%,#3d4b5c)"></div>

  <div class="abs sub-title" style="left:0;top:1381px;width:1200px">Our Partners</div>
  <svg class="abs" style="left:152px;top:1446px" width="14" height="24"><path d="M12 2L2 12l10 10" stroke="var(--teal)" stroke-width="3" fill="none"/></svg>
  <svg class="abs" style="left:1032px;top:1446px" width="14" height="24"><path d="M2 2l10 10L2 22" stroke="var(--teal)" stroke-width="3" fill="none"/></svg>
  <span class="abs" style="left:185px;top:1430px;width:60px;height:60px;border-radius:50%;background:var(--white)"></span>
  <span class="abs" style="left:330px;top:1446px;width:80px;height:24px;border-radius:12px;background:rgba(255,255,255,.8)"></span>
  <span class="abs" style="left:470px;top:1440px;width:105px;height:30px;border-radius:6px;background:rgba(255,255,255,.7)"></span>
  <span class="abs" style="left:645px;top:1438px;width:60px;height:36px;border-radius:6px;background:rgba(255,255,255,.6)"></span>
  <span class="abs" style="left:800px;top:1430px;width:60px;height:60px;border-radius:50%;background:rgba(255,255,255,.5)"></span>
  <span class="abs" style="left:945px;top:1446px;width:80px;height:24px;border-radius:12px;background:rgba(255,255,255,.4)"></span>
  <div class="abs" style="left:0;top:1521px;width:1200px;text-align:center"><span class="dot" style="background:#cde"></span><span class="dot" style="background:#cde"></span><span class="dot" style="background:var(--teal)"></span><span class="dot" style="background:#cde"></span></div>
</section>

<section class="abs testimonials">
  <svg class="abs" style="left:0;top:0" width="1200" height="521"><path d="M0 400C60 430 80 500 160 521H0Z" fill="var(--mint)"/><circle cx="1000" cy="500" r="170" fill="#e4e8ea"/></svg>
  <div class="abs" style="left:0;top:105px;width:1200px;text-align:center"><span class="heading-light" style="font-size:27px">Check What </span><span class="heading-bold" style="font-size:36px">Our Clients Say</span></div>
  <svg class="abs" style="left:561px;top:151px" width="80" height="16"><line x1="0" y1="8" x2="80" y2="8" stroke="var(--blue)" stroke-width="2.5"/><rect x="34" y="2" width="12" height="12" transform="rotate(45 40 8)" fill="var(--blue)"/></svg>
  <div class="quote-card" style="left:141px">"Lorem ipsum dolor sit amet, consectetur adipiscing elit, sed do eiusmod tempor incididunt ut labore et dolore magna aliqua. Vulputate dignissim suspendisse in est ante. Faucibus turpis in eu mi bibendum neque."</div>
  <div class="quote-card" style="left:613px">"Lorem ipsum dolor sit amet, consectetur adipiscing elit, sed do eiusmod tempor incididunt ut labore et dolore magna aliqua. Vulputate dignissim suspendisse in est ante. Faucibus turpis in eu mi bibendum neque."</div>
  <div class="client" style="left:182px"><div class="avatar" role="img" aria-label="Portrait of client"></div><div><div class="client-name">Clara Venn</div><div class="client-role">CEO &amp; Founder Lumaro</div></div></div>
  <div class="client" style="left:654px"><div class="avatar" role="img" aria-label="Portrait of client" style="background:#8a5a40"></div><div><div class="client-name">Theo Marsh</div><div class="client-role">Orbis CEO</div></div></div>
  <div class="abs" style="left:0;top:433px;width:1200px;text-align:center"><span class="dot" style="background:#f08a24"></span><span class="dot"></span><span class="dot"></span></div>
</section>

<footer class="abs footer">
  <div class="brand" style="left:482px;top:54px"><div class="brand-mark"></div><div class="brand-name" style="font-size:8.5px">Wellness, Meaning, and the Inner Journey<br><span style="color:var(--teal)">The Research Program</span></div></div>
  <div class="abs" style="left:520px;top:113px;display:flex;gap:15px"><span class="social"></span><span class="social"></span><span class="social"></span><span class="social"></span></div>
  <div class="contact-item" style="left:214px;top:163px;font-size:13px"><svg width="16" height="18" viewBox="0 0 16 18"><path d="M8 0a6 6 0 0 0-6 6c0 5 6 12 6 12s6-7 6-12a6 6 0 0 0-6-6zm0 8.5A2.5 2.5 0 1 1 8 3.5a2.5 2.5 0 0 1 0 5z" fill="var(--teal)"/></svg>#1011 Lakeview City, US</div>
  <div class="contact-item" style="left:466px;top:163px;font-size:13px"><svg width="16" height="16" viewBox="0 0 16 16"><path d="M3 1l3 3-2 2c1 2 3 4 5 5l2-2 3 3-2 3C6 15 1 10 1 3z" fill="var(--teal)"/></svg>+1 555 204 7781</div>
  <div class="contact-item" style="left:672px;top:163px;font-size:13px"><svg width="18" height="18" viewBox="0 0 18 18"><rect x="1" y="3" width="16" height="14" rx="2" fill="var(--teal)"/><rect x="4" y="6" width="10" height="3" fill="#fff"/></svg>+1 555 318 2406</div>
  <div class="contact-item" style="left:876px;top:163px;font-size:13px"><svg width="26" height="18" viewBox="0 0 26 18"><rect width="26" height="18" fill="var(--teal)"/><path d="M0 0l13 10L26 0" stroke="#fff" fill="none" stroke-width="1.5"/></svg>info@wmij.org</div>
  <span class="foot-link" style="left:204px">Home</span>
  <span class="foot-link" style="left:367px">About Us</span>
  <span class="foot-link" style="left:550px">Our Products</span>
  <span class="foot-link" style="left:757px">Services</span>
  <span class="foot-link" style="left:933px">Contact Us</span>
</footer>

</body>
</html>
```